Road Construction Company needs business cards

We would like a new business card designed for our business.

We're a road construction company based in Qld, Australia.

Can the business card please have the following information on it.

Name: Warren Halbeck
Position: General Manager
Phone: 0472 915 348
Email: Warren.halbeck@tovrin.com.au
Address: 87 Marrow Ave, Pendlebay, QLD, 4023
Website: www.tovrin.com.au

Visually we'd like the card to be professional and simple.

Attached is our logo.

Our website is www.tovrin.com.au

Target Market(s)

Men aged 25-60

Contact Information for Business Card

As listed in project description

Font styles to use
Serif

Requirements
Must have
• Large logo on back of card

```html
<!DOCTYPE html>
<html lang="en">
<head>
<meta charset="utf-8">
<title>Tovrin Business Card</title>
<link rel="stylesheet" href="https://fonts.googleapis.com/css2?family=Play:wght@400;700&family=Michroma&display=swap">
<style>
  :root {
    --backdrop: #d9d9d9;
    --navy: #0a52a3;
    --blue-deep: #05489c;
    --blue-mid: #1b7cc2;
    --blue-light: #2fa0d6;
    --sky: #2c96d2;
    --ink: #1a1a1a;
    --rule: #8a8a8a;
    --paper: #ffffff;
  }
  html, body {
    margin: 0;
    width: 1200px;
    height: 1200px;
    overflow: hidden;
    background: var(--backdrop);
  }
  .sheet {
    position: relative;
    width: 1200px;
    height: 1200px;
  }
  .card {
    position: absolute;
    top: 303px;
    width: 369px;
    height: 594px;
    box-sizing: border-box;
  }
  .card--back {
    left: 213px;
    background: linear-gradient(215deg, var(--blue-light) 0%, var(--blue-mid) 45%, var(--blue-deep) 80%);
    overflow: hidden;
  }
  .card--back .bands {
    position: absolute;
    inset: 0;
  }
  .card--back .brand {
    position: absolute;
    left: 0;
    right: 0;
    top: 470px;
    text-align: center;
    font-family: "Play", sans-serif;
    font-weight: 700;
    font-size: 46px;
    letter-spacing: 6px;
    color: var(--paper);
  }
  .card--front {
    left: 611px;
    width: 364px;
    background: var(--paper);
    text-align: center;
    font-family: "Play", sans-serif;
    color: var(--ink);
  }
  .card--front .brand {
    position: absolute;
    left: 0;
    right: 0;
    top: 142px;
    font-family: "Play", sans-serif;
    font-weight: 700;
    font-size: 46px;
    letter-spacing: 6px;
    color: var(--navy);
  }
  .person {
    position: absolute;
    left: 0;
    right: 0;
    top: 342px;
  }
  .person__name {
    font-family: "Michroma", sans-serif;
    font-weight: 400;
    font-size: 16px;
    letter-spacing: 0.5px;
    color: var(--navy);
    -webkit-text-stroke: 0.6px var(--navy);
    line-height: 22px;
  }
  .person__role {
    font-size: 16px;
    color: var(--sky);
    line-height: 18px;
  }
  .icon-row {
    position: absolute;
    left: 0;
    right: 0;
    top: 395px;
    display: flex;
    justify-content: center;
    align-items: center;
    gap: 4px;
  }
  .icon-row .rule {
    width: 52px;
    height: 1px;
    background: var(--rule);
    margin: 0 4px;
  }
  .icon {
    width: 25px;
    height: 25px;
    border-radius: 3px;
    background: var(--navy);
    display: flex;
    align-items: center;
    justify-content: center;
  }
  .contact {
    position: absolute;
    left: 0;
    right: 0;
    top: 432px;
    font-size: 17px;
    line-height: 21.5px;
  }
  .contact .accent { color: var(--navy); }
  .divider {
    position: absolute;
    left: 88px;
    width: 195px;
    top: 507px;
    height: 1px;
    background: var(--rule);
  }
  .address {
    position: absolute;
    left: 0;
    right: 0;
    top: 518px;
    font-size: 17px;
    line-height: 21.5px;
  }
</style>
</head>
<body>
<div class="sheet">

  <section class="card card--back" aria-label="Card back">
    <svg class="bands" width="369" height="594" viewBox="0 0 369 594" aria-hidden="true">
      <polygon points="0,594 0,380 240,0 369,0 369,0" fill="#ffffff" opacity="0.05"/>
      <polygon points="186,594 369,178 369,250 220,594" fill="#3fb0e2" opacity="0.35"/>
      <polygon points="148,594 369,262 369,280 158,594" fill="#ffffff" opacity="0.08"/>
      <polygon points="200,594 369,465 369,594" fill="#2fa0d6" opacity="0.35"/>
    </svg>
    <div class="brand">TOVRIN</div>
  </section>

  <section class="card card--front" aria-label="Card front">
    <div class="brand">TOVRIN</div>

    <div class="person">
      <div class="person__name">WARREN HALBECK</div>
      <div class="person__role">General Manager</div>
    </div>

    <div class="icon-row">
      <span class="rule"></span>
      <span class="icon" aria-label="Phone">
        <svg width="17" height="14" viewBox="0 0 17 14">
          <path d="M1 5 C1 1 16 1 16 5 L13 6 L12 4 C9 3 8 3 5 4 L4 6 Z" fill="#fff"/>
          <rect x="3.5" y="7" width="10" height="6" rx="1" fill="#fff"/>
        </svg>
      </span>
      <span class="icon" aria-label="Email">
        <svg width="17" height="13" viewBox="0 0 17 13">
          <rect x="1" y="1" width="15" height="11" fill="none" stroke="#fff" stroke-width="1.3"/>
          <path d="M1 1 L8.5 7.5 L16 1 M1 12 L6.5 6 M16 12 L10.5 6" fill="none" stroke="#fff" stroke-width="1.1"/>
        </svg>
      </span>
      <span class="icon" aria-label="Website">
        <svg width="17" height="17" viewBox="0 0 17 17">
          <circle cx="8.5" cy="8.5" r="7" fill="#fff"/>
          <path d="M5 4 C7 5 8 7 6 9 C5 10 6 12 7 14 M10 3 C12 5 13 7 11 9 L12 12" fill="none" stroke="#0a52a3" stroke-width="1.4"/>
        </svg>
      </span>
      <span class="rule"></span>
    </div>

    <div class="contact">
      <div>0472 915 348</div>
      <div>Warren.halbeck@tovrin.com.au</div>
      <div>www.<span class="accent">tovrin</span>.com.au</div>
    </div>

    <div class="divider"></div>

    <div class="address">
      <div>87 Marrow Ave</div>
      <div>Pendlebay, QLD, 4023</div>
    </div>
  </section>

</div>
</body>
</html>
```